Talvique Hotels Business Card and Logo

We need a business card design for a hotel group. I saw a hotel card you designed and really liked it. We have multiple properties with different brands. Were hoping that the card would be unique and find a way to list out all our properties. Our web address is www.talviquehotels.com. I have attached some photos of card designs I like.

Industry/Entity Type

Hotel

Contact Information for Business Card

Scott CurranReneson HotelsChief Operating Officer56 Madera DriveCorte Madera, CA 94925Office 415-891-5013Cell 707-5550143

```html
<!DOCTYPE html>
<html lang="en">
<head>
<meta charset="utf-8">
<title>Talvique Hotels Business Card</title>
<link rel="stylesheet" href="https://fonts.googleapis.com/css2?family=EB+Garamond:wght@400;600&display=swap">
<style>
  :root {
    --backdrop: #1c1c1d;
    --gold-light: #e6b94a;
    --gold-mid: #cfa033;
    --gold-deep: #a97c1b;
    --ink: #1a1712;
    --paper: #fbfbf9;
    --white: #ffffff;
  }
  * { margin: 0; padding: 0; box-sizing: border-box; }
  html, body {
    width: 1200px; height: 900px; overflow: hidden;
    background: var(--backdrop);
    font-family: "EB Garamond", Georgia, serif;
  }
  .card {
    position: absolute;
    width: 525px; height: 300px;
    box-shadow: 0 14px 30px rgba(0,0,0,.55);
    overflow: hidden;
  }
  .card-back {
    left: 110px; top: 110px;
    background: linear-gradient(115deg, var(--gold-deep) 0%, var(--gold-mid) 40%, var(--gold-light) 100%);
    color: var(--ink);
  }
  .card-back .brand-name {
    position: absolute; left: 0; right: 0; top: 108px;
    text-align: center;
    font-size: 40px; font-weight: 400; letter-spacing: 2px;
    text-transform: uppercase;
    color: var(--ink);
  }
  .card-back .web-address {
    position: absolute; left: 0; right: 0; bottom: 46px;
    text-align: center;
    font-size: 14px; letter-spacing: 3px;
    color: var(--ink);
  }
  .card-front {
    left: 565px; top: 480px;
    background: var(--paper);
  }
  .card-front .brand-name {
    position: absolute; left: 0; right: 0; top: 52px;
    text-align: center;
    font-size: 34px; font-weight: 400; letter-spacing: 2px;
    text-transform: uppercase;
    color: var(--gold-mid);
  }
  .info-band {
    position: absolute; left: 0; right: 0; bottom: 0; height: 132px;
    background: linear-gradient(110deg, var(--gold-deep) 0%, var(--gold-mid) 45%, var(--gold-light) 100%);
  }
  .band-rule {
    position: absolute; left: 0; right: 0; height: 2px;
    background: var(--gold-mid);
  }
  .band-rule.upper { bottom: 144px; }
  .band-rule.lower { bottom: 139px; }
  .band-inner-rule {
    position: absolute; left: 0; right: 0; top: 6px; height: 1.5px;
    background: var(--white);
  }
  .person-block {
    position: absolute; right: 280px; top: 28px;
    text-align: right; color: var(--white);
    line-height: 1.25;
  }
  .person-name { font-size: 17px; font-weight: 600; text-transform: uppercase; letter-spacing: .5px; }
  .person-title, .person-address { font-size: 14px; }
  .divider {
    position: absolute; left: 262px; top: 24px; width: 2px; height: 86px;
    background: var(--white);
  }
  .contact-list {
    position: absolute; left: 284px; top: 26px;
    list-style: none; color: var(--white); font-size: 14px;
  }
  .contact-list li { display: flex; align-items: center; gap: 10px; height: 26px; }
  .contact-icon {
    width: 18px; height: 18px; border-radius: 50%;
    background: var(--white);
    display: flex; align-items: center; justify-content: center;
  }
  .contact-icon svg { width: 11px; height: 11px; fill: var(--gold-deep); }
</style>
</head>
<body>

<section class="card card-back" aria-label="Card back">
  <div class="brand-name">Talvique Hotels</div>
  <div class="web-address">www.talviquehotels.com</div>
</section>

<section class="card card-front" aria-label="Card front">
  <div class="brand-name">Talvique Hotels</div>

  <div class="band-rule upper"></div>
  <div class="band-rule lower"></div>

  <div class="info-band">
    <div class="band-inner-rule"></div>

    <div class="person-block">
      <div class="person-name">Brent Holloway</div>
      <div class="person-title">Chief Operating Officer</div>
      <div class="person-address">83 Pellwick Lane</div>
      <div class="person-address">Larkfield, CA 94990</div>
    </div>

    <div class="divider"></div>

    <ul class="contact-list">
      <li>
        <span class="contact-icon">
          <svg viewBox="0 0 24 24"><path d="M6.6 10.8a15.1 15.1 0 0 0 6.6 6.6l2.2-2.2c.3-.3.7-.4 1-.2 1.1.4 2.3.6 3.6.6.6 0 1 .4 1 1V20c0 .6-.4 1-1 1A17 17 0 0 1 3 4c0-.6.4-1 1-1h3.5c.6 0 1 .4 1 1 0 1.3.2 2.5.6 3.6.1.3 0 .7-.2 1z"/></svg>
        </span>
        415-555-0186
      </li>
      <li>
        <span class="contact-icon">
          <svg viewBox="0 0 24 24"><path d="M6 3h12v5H6zM4 9h16a2 2 0 0 1 2 2v6h-4v4H6v-4H2v-6a2 2 0 0 1 2-2zm4 6v4h8v-4z"/></svg>
        </span>
        707-5550143
      </li>
      <li>
        <span class="contact-icon">
          <svg viewBox="0 0 24 24"><path d="M2 5h20v14H2zm2 2v.4l8 5.2 8-5.2V7zm0 2.8V17h16V9.8l-8 5.2z"/></svg>
        </span>
        BrentH@talviquehotels.com
      </li>
    </ul>
  </div>
</section>

</body>
</html>
```